School Website

I need a design for a School (2 sections: Primary 6-12 years and Secondary 12-18 years). The first page is just a choice of the 2 sections. After we'll need 2 websites (with the same structure: Menu, ...) but with different colors. In fact, we need for end of October, 6 design of school website. So the best websites are going to be made available to you in the future (in pixelharbor) but privately.

Target Market(s)

Public, Parents, ...

Coding

Coded - Design and coding required

Number of Pages Required

5+ page

Font styles to use
Sans Serif

Colors
34a6d7
85cae6
cee9f5
ffffff

Requirements
Must have
• You can check the old Website: http: / /velmot.be We need the same pages with the same content. Menu: - HomePage - News and communication (like blog page) - Activities (like blog page, with photo gallery) - Contact (Contact form + maps) - In the main menu, we need a special button to connect to an external Website ( button needs to be different than the other menu items The name of this button is "Parents Area"). The logo of 2 sections are attached. Please use it for the design and the choice of colors.
Nice to have
• This is a web design of other school that we like: https://www.quintelo.be

```html
<!DOCTYPE html>
<html lang="en">
<head>
<meta charset="utf-8">
<title>Royal Athenaeum De Velmot – Website</title>
<link href="https://fonts.googleapis.com/css2?family=Poppins:wght@400;500;600;700&family=Source+Sans+3:wght@400;600;700&display=swap" rel="stylesheet">
<style>
:root{
  --blue:#34a6d7;
  --blue-deep:#2a8fd0;
  --blue-mid:#85cae6;
  --blue-pale:#cee9f5;
  --navy:#1c3f6e;
  --ink:#222;
  --grey:#777;
  --board:#f1f1f1;
  --white:#fff;
  --dark:#22272e;
}
*{margin:0;padding:0;box-sizing:border-box}
html,body{width:702px;height:1200px;overflow:hidden;background:var(--board)}
body{font-family:"Source Sans 3",Arial,sans-serif;color:var(--ink)}
.board{position:absolute;left:0;top:0;width:1475px;height:2520px;transform:scale(.47593);transform-origin:0 0;background:var(--board)}
.page{position:absolute;background:var(--white);overflow:hidden}
.home{left:69px;top:110px;width:645px;height:2410px}
.choice{left:752px;top:110px;width:645px;height:481px}
.abs{position:absolute}
.poppins{font-family:"Poppins",Arial,sans-serif}
.photo{position:absolute}

/* top bar */
.topbar{left:0;top:0;width:645px;height:36px}
.topbar-text{color:var(--white);font-size:11px;top:11px}
.topbar-text.bold{font-weight:600;font-size:12px;top:10px}
.brand{display:flex;align-items:center;gap:7px;font-weight:700;color:var(--blue-deep);font-size:15px}
.brand-dot{width:24px;height:24px;border-radius:50%;background:var(--blue-deep)}
.nav{left:257px;top:62px;display:flex;gap:15px;font-size:9.5px;color:#333}
.nav .active{color:var(--blue)}

.hero-title{left:61px;top:202px;font-size:32px;font-weight:700;color:#1c1c1c}
.btn{position:absolute;display:flex;align-items:center;justify-content:center;background:var(--blue-deep);color:var(--white);font-family:"Poppins",Arial,sans-serif;font-weight:600;border-radius:20px}
.dot{position:absolute;width:10px;height:10px;border-radius:50%;background:var(--blue-deep);left:623px}

.welcome-kicker{left:48px;top:484px;font-size:21px;font-weight:400}
.welcome-title{left:48px;top:512px;font-size:21px;font-weight:700;color:var(--blue-deep)}
.welcome-copy{left:45px;top:550px;width:356px;font-size:8.6px;line-height:16.6px;color:#333}

.topic{position:absolute;width:116px;text-align:center}
.topic-pic{width:116px;height:116px;border-radius:50%;box-shadow:3px 6px 0 #111}
.topic-label{margin-top:28px;color:var(--white);font-weight:700;font-size:12px;line-height:18px}

.section-title{font-family:"Poppins",Arial,sans-serif;font-weight:600}
.news-card{position:absolute;background:var(--white);border:1px solid #cfcfcf}
.news-date{font-size:7.5px;color:var(--navy)}
.news-head{font-family:"Poppins",Arial,sans-serif;font-weight:600;font-size:11px;line-height:14px;margin-top:8px;color:#111}
.news-copy{font-size:7px;line-height:14.5px;color:#888;margin-top:5px}
.news-more{font-size:8.5px;font-weight:700;color:var(--blue-deep);margin-top:6px}

.comm-title{left:0;width:645px;top:1613px;text-align:center;color:var(--white);font-size:22px;font-weight:700}
.comm-copy{left:82px;width:480px;top:1657px;text-align:center;color:var(--white);font-size:9.6px;line-height:16.6px}

.field{position:absolute;border:1px solid #bbb;font-size:12px;color:var(--navy);padding:8px 13px;background:var(--white)}
.contact-title{left:323px;width:260px;top:1903px;text-align:center;color:var(--navy);font-size:20px;font-weight:600}

.foot-icon{position:absolute;width:34px;height:34px;border-radius:50%;background:var(--blue-deep);display:flex;align-items:center;justify-content:center}
.foot-text{position:absolute;color:var(--white);font-size:8.5px;text-align:center;line-height:15px}
.foot-nav{left:0;width:645px;top:2318px;display:flex;justify-content:center;gap:32px;color:var(--white);font-size:10.5px;padding-right:30px}
.foot-social{left:290px;top:2356px;display:flex;gap:10px}
.foot-social span{width:10px;height:10px;border-radius:50%;background:var(--white)}
.copyright{left:64px;top:2394px;color:var(--white);font-size:7px}

.section-card-label{position:absolute;top:406px;width:200px;text-align:center;font-size:15px;line-height:18px;font-weight:600}
.social-dot{position:absolute;top:445px;width:25px;height:25px;border-radius:50%;background:var(--blue-deep)}
</style>
</head>
<body>
<div class="board">

  <!-- Home page -->
  <main class="page home">
    <!-- top bar -->
    <svg class="abs topbar" viewBox="0 0 645 36" width="645" height="36">
      <rect width="645" height="36" fill="var(--blue-deep)"/>
      <path d="M0 0 H215 Q226 0 232 10 L244 30 Q248 36 258 36 H0 Z" fill="var(--white)"/>
    </svg>
    <svg class="abs" style="left:325px;top:13px" width="17" height="12" viewBox="0 0 17 12"><rect x=".5" y=".5" width="16" height="11" fill="none" stroke="#fff"/><path d="M.5 .5 8.5 7 16.5 .5" fill="none" stroke="#fff"/></svg>
    <span class="abs topbar-text" style="left:350px">info@velmot.be</span>
    <svg class="abs" style="left:469px;top:10px" width="14" height="14" viewBox="0 0 24 24"><path fill="#fff" d="M6.6 10.8a15.1 15.1 0 0 0 6.6 6.6l2.2-2.2c.3-.3.7-.4 1-.2 1.1.4 2.3.6 3.6.6.6 0 1 .4 1 1V20c0 .6-.4 1-1 1A17 17 0 0 1 3 4c0-.6.4-1 1-1h3.5c.6 0 1 .4 1 1 0 1.3.2 2.5.6 3.6.1.3 0 .7-.2 1z"/></svg>
    <span class="abs topbar-text bold" style="left:495px">+32 81 40 55 17</span>

    <div class="abs brand" style="left:48px;top:50px"><span class="brand-dot"></span>Athénée Royal de Velmot</div>
    <nav class="abs nav">
      <span class="active">Home</span><span>Kindergarten-Primary</span><span>Plan</span><span>In practice</span><span>Trip</span><span>News</span><span>Contact</span>
    </nav>

    <!-- hero -->
    <div class="photo" role="img" aria-label="Classroom with pupils raising their hands and a teacher at the board" style="left:0;top:91px;width:645px;height:354px;background:linear-gradient(120deg,#e9dcb6 0%,#d8b77a 40%,#b88c55 70%,#7a6a52 100%)"></div>
    <svg class="abs" style="left:0;top:345px" width="645" height="100" viewBox="0 0 645 100">
      <path d="M0 100 V90 C180 50 420 20 645 38 V100 Z" fill="var(--white)"/>
      <path d="M0 90 C180 50 420 20 645 38 V28 C430 8 200 35 0 84 Z" fill="var(--blue-deep)"/>
      <path d="M380 22 C460 10 560 12 645 24 V16 C560 6 460 6 380 22 Z" fill="var(--blue-deep)"/>
    </svg>
    <h1 class="abs hero-title poppins">Royal Athenaeum De Velmot</h1>
    <div class="btn" style="left:64px;top:262px;width:118px;height:36px;font-size:11px">Parents Area</div>
    <span class="dot" style="top:190px;background:#111"></span>
    <span class="dot" style="top:207px"></span>
    <span class="dot" style="top:223px"></span>

    <!-- welcome -->
    <div class="abs welcome-kicker poppins">Welcome To</div>
    <h2 class="abs welcome-title poppins">Royal Athenaeum De Velmot</h2>
    <p class="abs welcome-copy">The Royal Athenaeum of Velmot comes from a primary school that grew up in middle school before offering complete studies of humanities.It is the oldest Athenian in the region. This helped to give him a solid reputation. In fact, children who are able to go on to preparatory studies at colleges or universities have passed through our walls according to the desire of their parents to find an education open to all philosophies and religious or political opinions.The requirements of this type of study have led the successive directorates to remain attached to the disciplines necessary for the pursuit of studies,</p>
    <div class="btn" style="left:47px;top:688px;width:97px;height:29px;font-size:9.5px">Read More</div>
    <svg class="abs" style="left:418px;top:470px" width="222" height="222" viewBox="0 0 222 222">
      <circle cx="111" cy="111" r="98" fill="var(--blue-deep)"/>
      <circle cx="40" cy="30" r="6" fill="var(--blue-deep)"/><circle cx="196" cy="52" r="5" fill="var(--blue-deep)"/><circle cx="20" cy="170" r="4" fill="var(--blue-deep)"/><circle cx="190" cy="190" r="6" fill="var(--blue-deep)"/>
    </svg>
    <div class="photo" role="img" aria-label="Teacher helping young pupils with a drawing at a table" style="left:449px;top:501px;width:160px;height:160px;border-radius:50%;background:radial-gradient(circle at 60% 40%,#e9b866,#b6a58c 55%,#6c8fa8)"></div>

    <!-- topics band -->
    <svg class="abs" style="left:0;top:710px" width="645" height="400" viewBox="0 0 645 400">
      <defs>
        <linearGradient id="bandFill" x1="0" y1="0" x2="1" y2="1">
          <stop offset="0" stop-color="#3c9fd0"/><stop offset=".5" stop-color="#3aa3c8"/><stop offset="1" stop-color="#2f86c4"/>
        </linearGradient>
      </defs>
      <path d="M0 62 C200 20 420 -15 645 57 V320 C420 380 180 390 0 325 Z" fill="url(#bandFill)" role="img" aria-label="Pupils studying outdoors on the grass, tinted blue"/>
      <path d="M160 32 C330 -2 510 0 645 57" fill="none" stroke="#111" stroke-width="7"/>
      <path d="M0 325 C140 385 330 395 645 320" fill="none" stroke="#111" stroke-width="7"/>
    </svg>
    <div class="topic" style="left:44px;top:814px"><div class="topic-pic" role="img" aria-label="Teacher helping a pupil" style="background:linear-gradient(150deg,#d9d3cb,#b08a6c)"></div><div class="topic-label">Our Teaching Team</div></div>
    <div class="topic" style="left:194px;top:814px"><div class="topic-pic" role="img" aria-label="Calendar page with a pencil" style="background:linear-gradient(150deg,#f1f1f1,#c9ccd1)"></div><div class="topic-label">Our schedules<br>and daycare</div></div>
    <div class="topic" style="left:345px;top:814px"><div class="topic-pic" role="img" aria-label="Teacher with an open book" style="background:linear-gradient(150deg,#4a4d52,#1f2326)"></div><div class="topic-label">Rules of procedure</div></div>
    <div class="topic" style="left:498px;top:814px"><div class="topic-pic" role="img" aria-label="Children playing in the sea" style="background:linear-gradient(180deg,#5fa8e3,#7fd2d6 60%,#3db3c4)"></div><div class="topic-label">School holidays</div></div>

    <!-- news -->
    <h2 class="abs section-title" style="left:66px;top:1130px;font-size:20px">Our News</h2>
    <article class="news-card" style="left:60px;top:1201px;width:358px;height:143px">
      <div class="photo" role="img" aria-label="Students at desks in a classroom" style="left:2px;top:2px;width:137px;height:138px;background:linear-gradient(160deg,#c6ccd4,#9b7e6c 60%,#5d4a48)"></div>
      <div class="abs" style="left:155px;top:15px;width:190px">
        <div class="news-date">Aug,2019</div>
        <div class="news-head">Sed ut perspiciatis unde omnis iste natus error</div>
        <div class="news-copy">Ut enim ad minima veniam, quis nostrerci tationem ullam corporis suscipit laboriosan isi ut aliquid ex ea eprehenderitq utate velit .</div>
        <div class="news-more">READ MORE »</div>
      </div>
    </article>
    <article class="news-card" style="left:60px;top:1352px;width:358px;height:143px">
      <div class="photo" role="img" aria-label="Smiling students in class" style="left:2px;top:2px;width:137px;height:138px;background:linear-gradient(160deg,#b9c8d8,#a27a62 55%,#4b5a6b)"></div>
      <div class="abs" style="left:155px;top:15px;width:190px">
        <div class="news-date">Aug,2019</div>
        <div class="news-head">Sed ut perspiciatis unde omnis iste natus error</div>
        <div class="news-copy">Ut enim ad minima veniam, quis nostrerci tationem ullam corporis suscipit laboriosan isi ut aliquid ex ea eprehenderitq utate velit .</div>
        <div class="news-more">READ MORE »</div>
      </div>
    </article>
    <article class="news-card" style="left:430px;top:1203px;width:172px;height:290px">
      <div class="photo" role="img" aria-label="School poster for the primary and nursery sections" style="left:1px;top:1px;width:168px;height:120px;background:linear-gradient(160deg,#2a5fa8,#8fc2ec 55%,#ffffff)"></div>
      <div class="abs" style="left:17px;top:156px;width:145px">
        <div class="news-head" style="margin-top:0">Sed ut perspiciatis unde omnis iste natus</div>
        <div class="news-copy">Ut enim ad minima veniaquis nostreierci tationem ullam corpboriosan isi utliquid ex ea commodi eprehenderitq ui in ea voluptmmodate velit .</div>
        <div class="news-more" style="margin-top:12px">READ MORE</div>
      </div>
    </article>

    <!-- communications -->
    <svg class="abs" style="left:0;top:1530px" width="645" height="330" viewBox="0 0 645 330">
      <path d="M0 55 C160 -5 380 15 645 60 V250 C520 320 360 320 0 248 Z" fill="#3a9bd5" role="img" aria-label="Children in class, tinted blue"/>
      <path d="M0 55 C150 0 300 5 520 45" fill="none" stroke="#111" stroke-width="6"/>
      <path d="M0 248 C300 300 520 330 645 252" fill="none" stroke="#111" stroke-width="6"/>
    </svg>
    <h2 class="abs comm-title poppins">Communications and Actualités</h2>
    <p class="abs comm-copy">Lorem ipsum dolor sit amet, consectetur adipiscing elit, sed do eiusmod tempor incididunt ut labore et dolore magna aliqua. Quis ipsum suspendisse ultrices gravida. Risus commodo viverra maecenas accumsan lacus vel facilisis. Lorem ipsum dolor sit amet, consectetur adipiscing elit, sed do eiusmod tempor incididunt ut labore et dolore magna aliqua. Quis ipsum suspendisse ultrices gravida. Risus commodo viverra maecenas accumsan lacus vel facilisis.</p>

    <!-- contact -->
    <div class="photo" role="img" aria-label="Smiling boy with glasses and a school bag pointing upward" style="left:45px;top:1885px;width:250px;height:245px;border-radius:40% 40% 10% 10%;background:linear-gradient(170deg,#d9a873,#c5c2bf 55%,#8b8f96)"></div>
    <h2 class="abs contact-title poppins">Contact Us</h2>
    <div class="field" style="left:323px;top:1954px;width:127px;height:31px">Name</div>
    <div class="field" style="left:468px;top:1954px;width:127px;height:31px">Email</div>
    <div class="field" style="left:323px;top:1996px;width:272px;height:34px">Phone</div>
    <div class="field" style="left:323px;top:2040px;width:272px;height:64px">Message</div>
    <div class="abs" style="left:411px;top:2117px;width:107px;height:33px;background:var(--navy);color:#fff;font-size:12px;font-weight:600;display:flex;align-items:center;justify-content:center">SEND MESSAGE</div>

    <!-- footer -->
    <svg class="abs" style="left:0;top:2115px" width="645" height="295" viewBox="0 0 645 295">
      <path d="M0 20 C200 75 440 60 645 15 V295 H0 Z" fill="var(--dark)" role="img" aria-label="Pupils in a classroom, darkened"/>
      <path d="M0 10 C200 75 440 60 645 8 V25 C440 85 200 90 0 22 Z" fill="var(--blue-deep)"/>
      <path d="M300 60 C430 62 540 40 645 28 V40 C540 55 430 75 300 60 Z" fill="var(--white)"/>
    </svg>
    <div class="foot-icon" style="left:174px;top:2229px"><svg width="14" height="14" viewBox="0 0 24 24"><path fill="#fff" d="M6.6 10.8a15.1 15.1 0 0 0 6.6 6.6l2.2-2.2c.3-.3.7-.4 1-.2 1.1.4 2.3.6 3.6.6.6 0 1 .4 1 1V20c0 .6-.4 1-1 1A17 17 0 0 1 3 4c0-.6.4-1 1-1h3.5c.6 0 1 .4 1 1 0 1.3.2 2.5.6 3.6.1.3 0 .7-.2 1z"/></svg></div>
    <div class="foot-icon" style="left:311px;top:2229px"><svg width="12" height="16" viewBox="0 0 12 16"><path fill="#fff" d="M6 0a6 6 0 0 0-6 6c0 4.5 6 10 6 10s6-5.5 6-10a6 6 0 0 0-6-6zm0 8.5A2.5 2.5 0 1 1 6 3.5a2.5 2.5 0 0 1 0 5z"/></svg></div>
    <div class="foot-icon" style="left:440px;top:2229px"><svg width="14" height="10" viewBox="0 0 14 10"><rect width="14" height="10" rx="1" fill="#fff"/><path d="M0 1 7 6 14 1" fill="none" stroke="var(--blue-deep)" stroke-width="1.3"/></svg></div>
    <div class="foot-text" style="left:130px;width:135px;top:2274px">+32 81 40 55 17</div>
    <div class="foot-text" style="left:260px;width:145px;top:2274px">4120 Linden Ave Ste 88;<br>Brookfield, OR 97012</div>
    <div class="foot-text" style="left:395px;width:135px;top:2274px">info@velmot.be</div>
    <nav class="abs foot-nav"><span>Home</span><span>Jobs</span><span>Companies</span><span>About us</span><span>Contact Us</span></nav>
    <div class="abs foot-social"><span></span><span></span><span></span><span></span></div>
    <div class="abs" style="left:47px;top:2386px;width:525px;height:1px;background:#666"></div>
    <div class="abs copyright">© 2019 Copyrights Company Name | All Rights Reserved</div>
  </main>

  <!-- Section choice page -->
  <section class="page choice">
    <div class="photo" role="img" aria-label="Smiling secondary students sitting in a classroom" style="left:0;top:0;width:645px;height:350px;background:linear-gradient(120deg,#4b4540,#a98a72 35%,#c8b4a4 60%,#7f8a96 85%,#d7dde2)"></div>
    <svg class="abs" style="left:0;top:260px" width="645" height="110" viewBox="0 0 645 110">
      <path d="M0 88 C250 60 430 5 645 30 V110 H0 Z" fill="var(--white)"/>
      <path d="M0 85 C250 55 430 0 645 25 V50 C430 20 250 70 0 95 Z" fill="var(--blue-deep)"/>
    </svg>
    <div class="abs brand" style="left:24px;top:14px;background:#fff;padding:6px 8px;font-size:14px"><span class="brand-dot" style="width:20px;height:20px"></span>Athénée Royal de Velmot</div>
    <svg class="abs" style="left:28px;top:222px" width="170" height="170" viewBox="0 0 170 170"><circle cx="85" cy="85" r="82" fill="var(--blue-deep)"/></svg>
    <div class="photo" role="img" aria-label="Young children drawing at a table with their teacher" style="left:43px;top:237px;width:140px;height:140px;border-radius:50%;background:radial-gradient(circle at 60% 40%,#e9b866,#b6a58c 55%,#6c8fa8)"></div>
    <svg class="abs" style="left:240px;top:222px" width="170" height="170" viewBox="0 0 170 170"><circle cx="85" cy="85" r="82" fill="var(--blue-deep)"/></svg>
    <div class="photo" role="img" aria-label="Group of smiling teenagers giving a thumbs up" style="left:255px;top:237px;width:140px;height:140px;border-radius:50%;background:radial-gradient(circle at 50% 45%,#c99a7a,#b34a3e 60%,#9fb8d9)"></div>
    <div class="section-card-label" style="left:20px;color:var(--blue-deep)">Kindergarten-primary<br>section</div>
    <div class="section-card-label" style="left:232px;color:#111">Secondary section</div>
    <span class="social-dot" style="left:538px"></span>
    <span class="social-dot" style="left:571px"></span>
    <span class="social-dot" style="left:603px"></span>
  </section>

</div>
</body>
</html>
```